International Clinical Software Company needs a new business card design

We are looking for a new business card design for our company that has recently expanded into the UK market, making us a multinational company.
After having rebranded our website and produced a new style guide, we are looking for a business card that is creative and attention grabbing, while being consistent with the style and colour scheme used on the new website, www.plumvora.example
We produce care management technology for the aged care market, but the main aspect we aim to communicate is the human element of our software, and the way it assists in providing better care for aged people, and stronger relationships between aged people and the staff that care for them.
Our current business card is a dark green with gold text, which makes the text quite difficult to read, not very aesthetically appealing and the colour scheme looks quite dated.
We would like something fresh and modern, that can still be colourful but doesn't use large blocks of dark colour, and uses the colours within our logo.
Something tying in with the leaves that are used in our logo could work quite nicely, along with the Autumn/Fall colours of soft greens, yellows and reds (also in our existing logo). However also happy to look at fresh, completely out of the box ideas we may not have yet considered.
Target Market(s)
The people that receive this business card work in the aged card or health industry and are either corporate/management level staff or clinical (Registered Nurses, care workers etc.)
Industry/Entity Type
Health Product
Contact Information for Business Card
Company Name - BrindlewayCare
Company locations: United Kingdom, Australia, New Zealand
Staff Details:
Staff name: Derek Mallow
Staff job title: Executive Chairman
Staff email: d.mallow@plumvora.example
Office phone number: 01742 918576
Font styles to use
Other font styles liked:
- Calibri
Requirements
Must have
- Must include the BrindlewayCare brand name in it's current font
- Must include logo (3 leaves in gold circle)
- Must include Business Card Details
Nice to have
- Elements of gold
- White space
- Something autumn themed but not too cliched
Should not have
- No blue - used by a major competitor and we would like to differentiate from them
- Large blocks of dark green colour (the green that appears in our leaves on the logo on our current business card is the background colour and it is far too dark)

```html
<!DOCTYPE html>
<html lang="en">
<head>
<meta charset="utf-8">
<title>BrindlewayCare Business Card</title>
<link href="https://fonts.googleapis.com/css2?family=Open+Sans:wght@300;400;700&display=swap" rel="stylesheet">
<style>
  :root {
    --crimson: #b5173f;
    --crimson-deep: #8e0f30;
    --crimson-light: #c92a52;
    --leaf-green: #5c9a3a;
    --band-white: #f4f4f4;
    --gold: #e7b52c;
    --gold-soft: #f1d27a;
    --ink-white: #ffffff;
    --backdrop: #e9e4dc;
  }
  * { margin: 0; padding: 0; box-sizing: border-box; }
  html, body {
    width: 1200px;
    height: 1022px;
    overflow: hidden;
    background: var(--backdrop);
    font-family: "Open Sans", Calibri, Arial, sans-serif;
  }
  .business-card {
    position: absolute;
    left: 120px;
    top: 231px;
    width: 960px;
    height: 560px;
    border-radius: 24px;
    overflow: hidden;
    box-shadow: 0 18px 40px rgba(60, 30, 20, 0.25);
  }
  .card-shapes {
    position: absolute;
    inset: 0;
    width: 960px;
    height: 560px;
  }
  .brand-block {
    position: absolute;
    left: 0;
    top: 120px;
    width: 960px;
    text-align: center;
  }
  .brand-mark {
    display: block;
    width: 96px;
    height: 96px;
    margin: 0 auto 18px;
    border-radius: 50%;
    background: var(--band-white);
    border: 6px solid var(--gold);
  }
  .brand-name {
    font-weight: 300;
    font-size: 66px;
    letter-spacing: 1px;
    color: var(--ink-white);
    line-height: 1;
  }
  .staff-details {
    position: absolute;
    left: 56px;
    top: 392px;
  }
  .staff-name {
    font-weight: 700;
    font-size: 30px;
    letter-spacing: 1px;
    text-transform: uppercase;
    color: var(--ink-white);
  }
  .staff-title {
    font-weight: 400;
    font-size: 22px;
    color: var(--gold);
    margin-top: 2px;
  }
  .contact-list {
    position: absolute;
    right: 48px;
    top: 54px;
    list-style: none;
    text-align: right;
  }
  .contact-item {
    display: flex;
    justify-content: flex-end;
    align-items: center;
    gap: 12px;
    font-size: 21px;
    color: var(--ink-white);
    margin-bottom: 14px;
  }
  .contact-icon {
    width: 22px;
    height: 22px;
    flex: none;
  }
  .office-locations {
    position: absolute;
    right: 52px;
    bottom: 42px;
    font-size: 22px;
    color: var(--leaf-green);
  }
</style>
</head>
<body>
  <article class="business-card">
    <svg class="card-shapes" viewBox="0 0 960 560" aria-hidden="true">
      <defs>
        <linearGradient id="card-face" x1="0" y1="0" x2="1" y2="1">
          <stop offset="0" stop-color="var(--crimson-light)"/>
          <stop offset="0.6" stop-color="var(--crimson)"/>
          <stop offset="1" stop-color="var(--crimson-deep)"/>
        </linearGradient>
      </defs>
      <rect width="960" height="560" fill="url(#card-face)"/>
      <path class="accent-stripe" d="M0 548 C 320 520, 700 420, 960 270 L 960 300 C 700 450, 320 548, 0 560 Z" fill="var(--leaf-green)"/>
      <path class="lower-band" d="M0 560 C 320 548, 700 450, 960 300 L 960 560 Z" fill="var(--band-white)"/>
    </svg>

    <div class="brand-block">
      <span class="brand-mark"></span>
      <div class="brand-name">BrindlewayCare</div>
    </div>

    <div class="staff-details">
      <div class="staff-name">Derek Mallow</div>
      <div class="staff-title">Executive Chairman</div>
    </div>

    <ul class="contact-list">
      <li class="contact-item">
        <span>01742 918576</span>
        <svg class="contact-icon" viewBox="0 0 24 24" aria-hidden="true">
          <path d="M6.6 2.5 9.4 6.2 7.7 8.4c1.2 2.8 3.4 5 6.2 6.2l2.2-1.7 3.7 2.8-1.6 3.8C10.8 19.3 4.9 13.4 2.8 6.2Z" fill="none" stroke="var(--gold)" stroke-width="2" stroke-linejoin="round"/>
        </svg>
      </li>
      <li class="contact-item">
        <span>d.mallow@plumvora.example</span>
        <svg class="contact-icon" viewBox="0 0 24 24" aria-hidden="true">
          <rect x="3" y="5.5" width="18" height="13" fill="none" stroke="var(--gold)" stroke-width="2"/>
          <path d="M3 6.5 12 13l9-6.5" fill="none" stroke="var(--gold)" stroke-width="2"/>
        </svg>
      </li>
    </ul>

    <div class="office-locations">United Kingdom, Australia, New Zealand</div>
  </article>
</body>
</html>
```